Landing Page and Logo for Auto-Blogging Platform

I created a platform that allows users to start a blog for their business, hobby, charity, etc. I need a landing page where users can learn about the platform, benefits of consistent blogging, SEO value, plans/pricing, etc. The landing page needs to have multiple call to action buttons encouraging the visitor to register/sign up for a free trial.

In addition to the landing page, I need a page for users to establish the settings for their blog. This page should be a fairly simple form, intended for the user to enter a few details to set up their blog:
1. Name of Blog
2. Up to 10 topics and/or keywords the blog should focus on
3. Theme: Color-scheme and logo upload for blog.

I have attached the specifications of the platform's functionality so you can better understand how it works, plans/pricing, etc.

I also need a logo for the business. The name of the platform is PostNook.

Target Market(s)

Website owners, bloggers, business owners

Industry/Entity Type

Technology, Internet, web design

Coding

Coded - Design and coding required

Number of Pages Required

2 page

Colors
0054AA
0677BA
7BADD7
CADEEF
E8F1F8
0094D4
00A9DD
6FCCEA
C7EBF8
E9F6FB

Requirements
Must have
• Eye-catching design but fairly light on content (keep it simple and brief.)
Nice to have
• Eye-catching yet simple design, clean and easy to understand what we are offering.
Should not have
• Too much “wordy” and confusing content.

```html
<!DOCTYPE html>
<html lang="en">
<head>
<meta charset="utf-8">
<title>PostNook – Automate Your Blog Posting with AI</title>
<link rel="stylesheet" href="https://fonts.googleapis.com/css2?family=Lato:wght@400;700;900&display=swap">
<style>
:root{
  --blue:#0054AA;
  --blue-mid:#0677BA;
  --blue-bright:#0094D4;
  --cyan:#00A9DD;
  --sky:#6FCCEA;
  --pale:#E8F1F8;
  --pale-2:#CADEEF;
  --ink:#111418;
  --dark:#0b0d10;
  --text:#2a2f36;
  --muted:#7a8290;
  --white:#ffffff;
}
*{box-sizing:border-box;margin:0;padding:0}
html,body{width:1200px;height:3144px;overflow:hidden}
body{font-family:"Lato",Arial,sans-serif;color:var(--text);background:var(--white);position:relative}
.section{position:absolute;left:0;width:1200px;overflow:hidden}
.abs{position:absolute}
.btn{position:absolute;display:flex;align-items:center;justify-content:center;font-weight:700;font-size:15px;border-radius:3px}
.btn-blue{background:var(--blue);color:var(--white)}
.btn-ghost{border:2px solid var(--white);color:var(--white)}
.brand{display:flex;align-items:center;gap:12px;color:var(--white);font-weight:900;font-size:26px}
.brand-mark{width:36px;height:36px;border:3px solid var(--white);border-radius:4px}
.title-bar{display:flex;align-items:center;gap:14px;font-size:44px;font-weight:400;white-space:nowrap}
.title-bar::before{content:"";width:4px;height:46px;background:var(--blue-bright)}
.title-bar b{color:var(--blue);font-weight:700}

/* Hero */
.hero{top:0;height:545px;background:linear-gradient(90deg,#05080c 0%,#0c1420 45%,#22303e 100%)}
.hero-photo{position:absolute;right:0;top:0;width:640px;height:545px;background:linear-gradient(90deg,rgba(12,20,32,0) 0%,#3b4a5a 40%,#6b7a88 80%,#46525e 100%)}
.nav{position:absolute;top:26px;left:110px;right:110px;display:flex;align-items:center}
.nav-links{display:flex;gap:30px;margin-left:auto;margin-right:40px;font-size:15px;font-weight:700;color:var(--white)}
.nav-links .active{border:2px solid var(--white);padding:4px 8px;margin:-6px -8px}
.nav-cta{position:static;padding:12px 18px}
.hero-eyebrow{left:110px;top:140px;color:var(--white);font-size:26px;font-weight:700}
.hero-title{left:110px;top:180px;width:560px;color:var(--white);font-size:50px;line-height:1.12;font-weight:900}
.hero-title .hl{color:var(--blue-bright)}
.hero-copy{left:110px;top:308px;width:440px;color:#d7dde4;font-size:13px;line-height:1.5}

/* About */
.about{top:545px;height:490px;background:var(--white)}
.about-photo{left:105px;top:100px;width:455px;height:290px;background:linear-gradient(135deg,#c9ccd0,#8f9aa6 55%,#5e6b78)}
.corner{position:absolute;width:36px;height:36px;border:4px solid var(--ink)}
.about-title{left:640px;top:92px}
.about-copy{left:660px;top:170px;width:420px;font-size:13px;line-height:1.65;color:var(--muted)}
.about-copy p+p{margin-top:10px}

/* Methods */
.methods{top:1035px;height:585px;background:linear-gradient(90deg,#08090b 0%,#15191e 45%,#2b2622 70%,#4b3e32 100%)}
.methods-photo{right:0;top:0;width:560px;height:585px;background:linear-gradient(90deg,rgba(20,22,26,0),#5b4a3a 45%,#3a3129 100%)}
.methods-title{left:110px;top:62px;color:var(--white)}
.methods-title b{color:var(--white)}
.method{left:110px;width:540px;display:flex;align-items:center;gap:30px;color:var(--white);font-size:15px;font-weight:700;line-height:1.4}
.method-icon{flex:none;width:42px;height:42px;background:var(--blue-mid);border:2px solid var(--sky);display:flex;align-items:center;justify-content:center}
.method-line{left:130px;width:2px;border-left:2px dashed var(--white);height:40px}
.btn-light{background:var(--white);color:var(--ink)}

/* Pricing */
.pricing{top:1620px;height:695px;background:var(--white)}
.pricing-title{left:0;right:0;top:58px;justify-content:center}
.plan{position:absolute;background:var(--white);text-align:center;box-shadow:0 6px 22px rgba(0,0,0,.13)}
.plan-head{background:#e9ebed;border-radius:0 0 50% 50%/0 0 22% 22%;padding-top:26px;height:150px}
.plan-name{font-size:20px;font-weight:700;color:var(--text)}
.plan-price{font-size:40px;font-weight:700;color:var(--blue);margin-top:8px}
.plan-price small{font-size:28px}
.plan-per{font-size:15px;color:var(--text);margin-top:4px}
.plan ul{list-style:none;text-align:left;padding:32px 0 0 40px}
.plan li{display:flex;align-items:center;gap:14px;font-size:13px;color:var(--text);height:36px}
.tick{width:16px;height:16px;border-radius:50%;background:var(--blue);flex:none;display:flex;align-items:center;justify-content:center}
.plan-btn{position:absolute;left:50%;transform:translateX(-50%);width:104px;height:36px;background:var(--pale-2);color:var(--text);font-size:13px;font-weight:700;display:flex;align-items:center;justify-content:center}
.plan--featured{z-index:2;box-shadow:0 10px 30px rgba(0,0,0,.2)}
.plan--featured .plan-head{background:var(--blue);color:var(--white)}
.plan--featured .plan-name,.plan--featured .plan-price,.plan--featured .plan-per{color:var(--white)}
.plan--featured .plan-btn{background:var(--blue);color:var(--white)}

/* How it works */
.how{top:2315px;height:450px;background:linear-gradient(90deg,#0a3f85,#0054AA 40%,#1a66b6 70%,#0b4792)}
.how-title{left:0;right:0;top:50px;justify-content:center;color:var(--white)}
.how-title::before{background:var(--white)}
.how-title b{color:var(--white)}
.step{position:absolute;top:135px;width:225px;text-align:center;color:var(--white)}
.step-icon{margin:0 auto;width:100px;height:100px;background:var(--white);display:flex;align-items:center;justify-content:center}
.step-bar{margin-top:20px;height:46px;background:var(--white);color:var(--ink);font-size:22px;font-weight:700;display:flex;align-items:center;justify-content:center;clip-path:polygon(0 0,92% 0,100% 50%,92% 100%,0 100%)}
.step-text{margin-top:16px;font-size:15px;line-height:1.4}

/* Footer */
.footer{top:2765px;height:379px;background:var(--dark);color:var(--white)}
.footer .brand{position:absolute;left:110px;top:50px;font-size:34px}
.footer .brand-mark{width:50px;height:50px}
.subscribe-input{left:110px;top:190px;width:300px;height:46px;background:var(--white);color:var(--muted);font-size:14px;display:flex;align-items:center;padding-left:16px}
.subscribe-btn{left:110px;top:252px;width:110px;height:40px;font-size:14px}
.fcol{position:absolute;top:45px;font-size:13px}
.fcol h4{font-size:18px;font-weight:700;margin-bottom:12px}
.fcol li{list-style:none;line-height:24px;color:#d6dadf}
.contact-row{display:flex;align-items:center;gap:12px;color:#d6dadf;margin-bottom:18px;white-space:nowrap}
.cicon{width:26px;height:26px;border-radius:50%;background:var(--blue);flex:none;display:flex;align-items:center;justify-content:center}
.socials{display:flex;gap:8px;margin-top:10px}
.socials span{width:24px;height:24px;background:var(--white)}
.copyright{left:0;right:0;bottom:0;height:44px;border-top:1px solid #2a2e33;display:flex;align-items:center;justify-content:center;font-size:12px;color:#b8bec6}
</style>
</head>
<body>

<!-- Hero -->
<header class="section hero">
  <div class="hero-photo" role="img" aria-label="Photo of a smiling businessman with glasses working on a laptop"></div>
  <nav class="nav">
    <div class="brand"><span class="brand-mark"></span>PostNook</div>
    <div class="nav-links">
      <span class="active">Home</span><span>About Us</span><span>Methods</span><span>Pricing</span><span>Benefits</span>
    </div>
    <div class="btn btn-blue nav-cta">Contact Us</div>
  </nav>
  <div class="abs hero-eyebrow">Welcome To</div>
  <h1 class="abs hero-title"><span class="hl">Automate</span> Your Blog Posting <span class="hl">with AI</span></h1>
  <p class="abs hero-copy">Transform your blogging experience with our AI-powered platform that not only generates and optimizes content tailored to your audience but also continuously learns and adapts to deliver smarter insights, keeping your voice steady in a crowded digital landscape.</p>
  <div class="btn btn-blue" style="left:110px;top:412px;width:176px;height:42px">Sign Up For a Free Trial</div>
  <div class="btn btn-ghost" style="left:302px;top:412px;width:118px;height:42px">Register Now</div>
</header>

<!-- About -->
<section class="section about">
  <span class="corner" style="left:88px;top:83px;border-right:none;border-bottom:none"></span>
  <div class="abs about-photo" role="img" aria-label="Photo of two colleagues reviewing work together at a laptop"></div>
  <span class="corner" style="left:541px;top:371px;border-left:none;border-top:none"></span>
  <h2 class="abs title-bar about-title"><span>About The <b>Platform</b></span></h2>
  <div class="abs about-copy">
    <p>The purpose of this platform is to allow anyone to start a blog and automate the process of creating content and posting it to the blog. Here is what the platform will provide for each user.</p>
    <p>Each post is written to be relevant to its audience and stays aligned to the topics you choose. It updates with current ideas and publishes on your schedule.</p>
  </div>
  <div class="btn btn-blue" style="left:660px;top:330px;width:110px;height:40px">Read More</div>
</section>

<!-- Methods -->
<section class="section methods">
  <div class="abs methods-photo" role="img" aria-label="Photo of a woman working at a laptop in a dim office"></div>
  <h2 class="abs title-bar methods-title"><span><b>Our Methods</b></span></h2>
  <div class="abs method" style="top:165px">
    <span class="method-icon"><svg width="24" height="24" viewBox="0 0 24 24" fill="none" stroke="#fff" stroke-width="2"><rect x="3" y="4" width="18" height="16"/><line x1="3" y1="10" x2="21" y2="10"/><line x1="9" y1="4" x2="9" y2="20"/></svg></span>
    <span>The user enters them into a table manually</span>
  </div>
  <div class="abs method-line" style="top:214px"></div>
  <div class="abs method" style="top:260px">
    <span class="method-icon"><svg width="24" height="24" viewBox="0 0 24 24" fill="none" stroke="#fff" stroke-width="2"><path d="M6 3h9l4 4v14H6z"/><path d="M12 17v-7M9 13l3-3 3 3"/></svg></span>
    <span>The user uploads a list of blog topics in CSV format</span>
  </div>
  <div class="abs method-line" style="top:309px"></div>
  <div class="abs method" style="top:355px">
    <span class="method-icon"><svg width="24" height="24" viewBox="0 0 24 24" fill="none" stroke="#fff" stroke-width="2"><rect x="5" y="7" width="14" height="12" rx="2"/><circle cx="9.5" cy="13" r="1.5"/><circle cx="14.5" cy="13" r="1.5"/><line x1="12" y1="3" x2="12" y2="7"/></svg></span>
    <span>AI can create the list of blog topics based on a prompt such as: "Provide a list of 52 blog topics for a handyman business's blog</span>
  </div>
  <div class="btn btn-light" style="left:110px;top:480px;width:110px;height:40px">Read More</div>
</section>

<!-- Pricing -->
<section class="section pricing">
  <h2 class="abs title-bar pricing-title"><span>Our <b>Pricing</b></span></h2>

  <div class="plan" style="left:200px;top:170px;width:265px;height:430px">
    <div class="plan-head"><div class="plan-name">Base Plan</div><div class="plan-price">$9.99<small>mo.</small></div><div class="plan-per">Every Month</div></div>
    <ul>
      <li><span class="tick"><svg width="10" height="10" viewBox="0 0 10 10"><path d="M2 5l2 2 4-4" stroke="#fff" stroke-width="1.6" fill="none"/></svg></span>1 blog post (up to 2,000 words)</li>
      <li><span class="tick"><svg width="10" height="10" viewBox="0 0 10 10"><path d="M2 5l2 2 4-4" stroke="#fff" stroke-width="1.6" fill="none"/></svg></span>Lorem ipsum dolor sit amet.</li>
      <li><span class="tick"><svg width="10" height="10" viewBox="0 0 10 10"><path d="M2 5l2 2 4-4" stroke="#fff" stroke-width="1.6" fill="none"/></svg></span>Lorem ipsum dolor sit amet.</li>
      <li><span class="tick"><svg width="10" height="10" viewBox="0 0 10 10"><path d="M2 5l2 2 4-4" stroke="#fff" stroke-width="1.6" fill="none"/></svg></span>Lorem ipsum dolor sit amet.</li>
    </ul>
    <div class="plan-btn" style="bottom:40px">Select Plan</div>
  </div>

  <div class="plan plan--featured" style="left:465px;top:140px;width:270px;height:490px">
    <div class="plan-head" style="height:170px;padding-top:36px"><div class="plan-name">Premium Plan</div><div class="plan-price">$14.99<small>/mo.</small></div><div class="plan-per">Every Week</div></div>
    <ul>
      <li><span class="tick"><svg width="10" height="10" viewBox="0 0 10 10"><path d="M2 5l2 2 4-4" stroke="#fff" stroke-width="1.6" fill="none"/></svg></span>1 blog post (up to 2,000 words)</li>
      <li><span class="tick"><svg width="10" height="10" viewBox="0 0 10 10"><path d="M2 5l2 2 4-4" stroke="#fff" stroke-width="1.6" fill="none"/></svg></span>Lorem ipsum dolor sit amet.</li>
      <li><span class="tick"><svg width="10" height="10" viewBox="0 0 10 10"><path d="M2 5l2 2 4-4" stroke="#fff" stroke-width="1.6" fill="none"/></svg></span>Lorem ipsum dolor sit amet.</li>
      <li><span class="tick"><svg width="10" height="10" viewBox="0 0 10 10"><path d="M2 5l2 2 4-4" stroke="#fff" stroke-width="1.6" fill="none"/></svg></span>Lorem ipsum dolor sit amet.</li>
    </ul>
    <div class="plan-btn" style="bottom:50px">Select Plan</div>
  </div>

  <div class="plan" style="left:735px;top:170px;width:265px;height:430px">
    <div class="plan-head"><div class="plan-name">Ultimate Plan</div><div class="plan-price">$24.99<small>/mo</small></div><div class="plan-per">Per Day</div></div>
    <ul>
      <li><span class="tick"><svg width="10" height="10" viewBox="0 0 10 10"><path d="M2 5l2 2 4-4" stroke="#fff" stroke-width="1.6" fill="none"/></svg></span>1 blog post (up to 2,000 words)</li>
      <li><span class="tick"><svg width="10" height="10" viewBox="0 0 10 10"><path d="M2 5l2 2 4-4" stroke="#fff" stroke-width="1.6" fill="none"/></svg></span>Lorem ipsum dolor sit amet.</li>
      <li><span class="tick"><svg width="10" height="10" viewBox="0 0 10 10"><path d="M2 5l2 2 4-4" stroke="#fff" stroke-width="1.6" fill="none"/></svg></span>Lorem ipsum dolor sit amet.</li>
      <li><span class="tick"><svg width="10" height="10" viewBox="0 0 10 10"><path d="M2 5l2 2 4-4" stroke="#fff" stroke-width="1.6" fill="none"/></svg></span>Lorem ipsum dolor sit amet.</li>
    </ul>
    <div class="plan-btn" style="bottom:40px">Select Plan</div>
  </div>
</section>

<!-- How it works -->
<section class="section how" role="img" aria-label="Blue-tinted photo of a team working at a table">
  <h2 class="abs title-bar how-title"><span>How <b>It Works</b></span></h2>
  <div class="step" style="left:130px">
    <div class="step-icon"><svg width="50" height="50" viewBox="0 0 24 24" fill="none" stroke="#0054AA" stroke-width="1.6"><rect x="4" y="3" width="16" height="18"/><line x1="8" y1="8" x2="16" y2="8"/><line x1="8" y1="12" x2="16" y2="12"/><line x1="8" y1="16" x2="13" y2="16"/></svg></div>
    <div class="step-bar">Step 1</div>
    <div class="step-text">Select frequency of<br>Automated Blog Posts</div>
  </div>
  <div class="step" style="left:360px">
    <div class="step-icon"><svg width="50" height="50" viewBox="0 0 24 24" fill="none" stroke="#0054AA" stroke-width="1.6"><rect x="3" y="5" width="14" height="14"/><path d="M10 14l9-9 2 2-9 9-3 1z"/></svg></div>
    <div class="step-bar">Step 2</div>
    <div class="step-text">Name your blog</div>
  </div>
  <div class="step" style="left:590px">
    <div class="step-icon"><svg width="50" height="50" viewBox="0 0 24 24" fill="none" stroke="#0054AA" stroke-width="1.6"><path d="M2 9l10-5 10 5-10 5z"/><path d="M6 11v5c3 2 9 2 12 0v-5"/></svg></div>
    <div class="step-bar">Step 3</div>
    <div class="step-text">Select your blog topics<br>(or let AI choose them<br>for you)</div>
  </div>
  <div class="step" style="left:820px">
    <div class="step-icon"><svg width="50" height="50" viewBox="0 0 24 24" fill="none" stroke="#0054AA" stroke-width="1.6"><path d="M4 20l2-6L17 3l4 4L10 18z"/><line x1="14" y1="6" x2="18" y2="10"/></svg></div>
    <div class="step-bar">Step 4</div>
    <div class="step-text">Go do something else and let<br>AI do all your blogging for<br>you!</div>
  </div>
</section>

<!-- Footer -->
<footer class="section footer">
  <div class="brand"><span class="brand-mark"></span>PostNook</div>
  <div class="abs subscribe-input">Enter Email Address</div>
  <div class="btn btn-blue subscribe-btn">Subscribe</div>

  <div class="fcol" style="left:505px">
    <h4>Quick Links</h4>
    <ul><li>Home</li><li>About Us</li><li>Methods</li><li>Pricing</li><li>Benefits</li><li>Contact Us</li></ul>
  </div>
  <div class="fcol" style="left:695px">
    <h4>Help Links</h4>
    <ul><li>Privacy Policy</li><li>Terms &amp; Conditions</li><li>Disclaimer</li></ul>
    <h4 style="margin-top:22px;margin-bottom:4px">Follow Us</h4>
    <div class="socials"><span></span><span></span><span></span><span></span></div>
  </div>
  <div class="fcol" style="left:890px">
    <h4>Contact Info</h4>
    <div class="contact-row"><span class="cicon"><svg width="12" height="12" viewBox="0 0 24 24" fill="#fff"><path d="M12 2a7 7 0 0 0-7 7c0 5 7 13 7 13s7-8 7-13a7 7 0 0 0-7-7zm0 9.5a2.5 2.5 0 1 1 0-5 2.5 2.5 0 0 1 0 5z"/></svg></span>Harbor Lane 12, Brookfield 40210</div>
    <div class="contact-row"><span class="cicon"><svg width="12" height="12" viewBox="0 0 24 24" fill="#fff"><path d="M6.6 10.8a15 15 0 0 0 6.6 6.6l2.2-2.2a1 1 0 0 1 1-.25 11 11 0 0 0 3.6.6 1 1 0 0 1 1 1V20a1 1 0 0 1-1 1A17 17 0 0 1 3 4a1 1 0 0 1 1-1h3.5a1 1 0 0 1 1 1 11 11 0 0 0 .6 3.6 1 1 0 0 1-.25 1z"/></svg></span>+1 555 010 2040</div>
    <div class="contact-row"><span class="cicon"><svg width="12" height="12" viewBox="0 0 24 24" fill="none" stroke="#fff" stroke-width="2.4"><rect x="3" y="5" width="18" height="14"/><path d="M3 6l9 7 9-7"/></svg></span>hello@postnook.io</div>
  </div>
  <div class="abs copyright">© 2024 PostNook, All Rights Reserved</div>
</footer>

</body>
</html>
```